Quillmarsh Property Solutions need a business card design

Hello guys. We would need a business card design asap please.
We are a start up property investment business based in London UK specialised in buying, selling, managing and letting properties and helping distressed property owners.
The name of our Business is Quillmarsh, the logo symbolises the four fundamental elements of the world (earth, air, fire and water) and so it stands for strength, stability, longevity.
We would like the business card to communicate professionalism and reliability. Many many thanks indeed for your work.

Details:

1.) Rosalind Updike
Property Investor
Mobile: +44(0)7700123456
Email: rosalind.quillmarsh@mailbox-example.com

2.) Dominic Updike
Property Investor
Mobile: +44(0)7700987654
Email: dominic.quillmarsh@mailbox-example.com

```html
<!DOCTYPE html>
<html lang="en">
<head>
<meta charset="utf-8">
<title>Quillmarsh Property Solutions – Business Cards</title>
<link rel="stylesheet" href="https://fonts.googleapis.com/css2?family=Montserrat:wght@800&family=Source+Sans+3:wght@400;600&display=swap">
<style>
  :root {
    --backdrop: #ecebe8;
    --card: #ffffff;
    --brand-green: #1b6a3b;
    --ink: #111111;
    --text-grey: #4a4f57;
    --rule-grey: #b9bcc0;
    --icon-blue: #3a6f9e;
  }
  * { box-sizing: border-box; margin: 0; padding: 0; }
  html, body {
    width: 1200px;
    height: 720px;
    overflow: hidden;
    background: var(--backdrop);
  }
  .canvas {
    position: relative;
    width: 1200px;
    height: 720px;
  }
  .card {
    position: absolute;
    width: 540px;
    height: 309px;
    background: var(--card);
    box-shadow: 0 2px 6px rgba(0,0,0,0.12);
    overflow: hidden;
  }
  /* ---------- front ---------- */
  .card--front { left: 50px; top: 70px; }
  .card__top-rule {
    position: absolute;
    left: 0; right: 0; top: 24px;
    height: 1px;
    background: var(--rule-grey);
  }
  .card__name-band {
    position: absolute;
    left: 0; right: 0; top: 32px;
    height: 40px;
    background: var(--brand-green);
    display: flex;
    align-items: center;
    justify-content: center;
    color: #fff;
    font-family: 'Source Sans 3', sans-serif;
    font-size: 17px;
    letter-spacing: 0.3px;
  }
  .card__name {
    font-weight: 600;
    text-transform: uppercase;
  }
  .card__role { font-weight: 400; margin-left: 4px; }
  .card__bottom-rule {
    position: absolute;
    left: 0; right: 0; bottom: 14px;
    height: 3px;
    background: var(--brand-green);
  }
  .brand {
    position: absolute;
    left: 40px; top: 148px;
    width: 200px;
    text-align: center;
    font-family: 'Montserrat', sans-serif;
    font-weight: 800;
    color: var(--ink);
  }
  .brand__square {
    display: block;
    width: 14px; height: 14px;
    margin: 0 auto 14px;
    background: var(--brand-green);
  }
  .brand__name { display: block; font-size: 21px; letter-spacing: 1px; }
  .brand__tagline { display: block; font-size: 9.5px; letter-spacing: 0.6px; margin-top: 3px; }
  .divider {
    position: absolute;
    left: 262px; top: 112px;
    width: 1px; height: 96px;
    background: var(--rule-grey);
  }
  .contacts {
    position: absolute;
    left: 282px; top: 124px;
    list-style: none;
    font-family: 'Source Sans 3', sans-serif;
    font-size: 14px;
    color: var(--text-grey);
  }
  .contacts__item {
    display: flex;
    align-items: center;
    gap: 9px;
    margin-bottom: 14px;
  }
  .contacts__icon { width: 13px; height: 13px; flex: none; }
  /* ---------- back ---------- */
  .card--back { left: 610px; top: 340px; }
  .wordmark {
    position: absolute;
    inset: 0;
    display: flex;
    flex-direction: column;
    align-items: center;
    justify-content: center;
    font-family: 'Montserrat', sans-serif;
    font-weight: 800;
    color: var(--ink);
    text-transform: uppercase;
  }
  .wordmark__name { font-size: 44px; letter-spacing: 2px; line-height: 1.1; }
  .wordmark__tagline { font-size: 21px; letter-spacing: 1.2px; margin-top: 6px; }
</style>
</head>
<body>
<main class="canvas">

  <section class="card card--front" aria-label="Business card front">
    <div class="card__top-rule"></div>
    <div class="card__name-band">
      <span class="card__name">Dominic Updike,</span><span class="card__role">Property Investor</span>
    </div>

    <div class="brand">
      <span class="brand__square"></span>
      <span class="brand__name">QUILLMARSH</span>
      <span class="brand__tagline">PROPERTY SOLUTIONS</span>
    </div>

    <div class="divider"></div>

    <ul class="contacts">
      <li class="contacts__item">
        <svg class="contacts__icon" viewBox="0 0 16 16" aria-hidden="true">
          <rect x="4" y="1" width="8" height="14" rx="1.5" fill="var(--icon-blue)"/>
          <rect x="5.5" y="3" width="5" height="7" fill="#fff"/>
          <circle cx="8" cy="12.5" r="0.9" fill="#fff"/>
        </svg>
        <span>+44(0)7700987654</span>
      </li>
      <li class="contacts__item">
        <svg class="contacts__icon" viewBox="0 0 16 16" aria-hidden="true">
          <rect x="1" y="3.5" width="14" height="9.5" rx="1.5" fill="var(--icon-blue)"/>
          <path d="M2 4.5 L8 9 L14 4.5" fill="none" stroke="#fff" stroke-width="1.3"/>
        </svg>
        <span>dominic.quillmarsh@mailbox-example.com</span>
      </li>
    </ul>

    <div class="card__bottom-rule"></div>
  </section>

  <section class="card card--back" aria-label="Business card back">
    <div class="wordmark">
      <span class="wordmark__name">Quillmarsh</span>
      <span class="wordmark__tagline">Property Solutions</span>
    </div>
  </section>

</main>
</body>
</html>
```